Wordpress design for media production company

We are a small production company called Copper Lantern Films specializing in documentary and short film.

We are after a wordpress web site that is fun and engaging with a relaxed feel. We would like to be able to easily edit and maintain the website ourselves.

We would like:
* A title screen that has a photo taking up most of the screen.
* Contact details (inc. social media links) on a static bar at the bottom.
* An area for our previous work. Some thumbnails or icons that open up and embedded youtube or vimeo video.
* An area for "about us" which will have information on the company and links to separate profiles of 3 (initially) employees.
* A Blog.
* Somewhere to show what we are currently working on.
* Examples of other stuff we have done (ie. photography, poetry, audio, animation and VFX).

We already have a logo that can be animated. It would be very cool to have it as a "Loading" page while things load in the background.

The text needs to be fun but easy to read.

We already have a license for "Q Layout" which seems pretty cool and flexible, so if you wanted to use it then great but if not then that is fine too.

A couple of pages that we like are:
http://www.plumorchardworks.com/
http://dorianvelkot.com/
http://www.spinthegrove.com/

Please do not hesitate to contact me if you would like more information on anything.

Cheers

Gideon

Target Market(s)

Mainly Australian clients seeking media services
Broadcasting companies

Industry/Entity Type

It Company

Requirements
Nice to have
• I love the parallax look on http://www.plumorchardworks.com/

```html
<!DOCTYPE html>
<html lang="en">
<head>
<meta charset="utf-8">
<title>Copper Lantern Films</title>
<link href="https://fonts.googleapis.com/css2?family=Open+Sans:wght@400;600;700;800&display=swap" rel="stylesheet">
<style>
:root{
  --black:#0b0b0b;
  --night:#141414;
  --card:#1d1d1d;
  --card-lite:#2a2a2a;
  --red:#c3121b;
  --white:#ffffff;
  --paper:#f4f4f4;
  --ink:#1a1a1a;
  --grey:#8a8a8a;
  --line:#d5d5d5;
}
*{box-sizing:border-box;margin:0;padding:0}
html,body{width:1200px;height:4500px;overflow:hidden;background:var(--white)}
body{position:relative;font-family:"Open Sans",Arial,sans-serif;color:var(--ink)}
.abs{position:absolute}
.section-title{position:absolute;left:180px;font-size:15px;font-weight:700;letter-spacing:.5px;text-transform:uppercase}
.section-title .tag{display:inline-block;background:var(--red);color:var(--white);padding:1px 5px;margin-left:3px}
.on-dark{color:var(--white)}
.body-copy{font-size:11px;line-height:17px;color:var(--grey)}
.photo{position:absolute}
.dot-nav{position:absolute;left:1156px;display:flex;flex-direction:column;gap:14px}
.dot-nav span{width:10px;height:10px;border-radius:50%;border:2px solid var(--grey);background:transparent}
.dot-nav span.active{background:var(--grey)}
.on-black .dot-nav span{border-color:#bbb}
.btn-outline{position:absolute;border:2px solid currentColor;font-size:10px;font-weight:700;letter-spacing:1px;text-align:center;line-height:30px;height:34px;text-transform:uppercase}

/* header + hero */
.hero{position:absolute;left:0;top:0;width:1200px;height:700px;
  background:linear-gradient(180deg,#9a9a9a 0%,#d9d9d9 38%,#6c6c6c 60%,#3b3b3b 80%,#7d7d7d 100%);
  clip-path:polygon(0 0,100% 0,100% 650px,0 700px)}
.main-nav{position:absolute;left:0;top:0;width:1200px;height:64px;background:rgba(0,0,0,.85)}
.main-nav a{position:absolute;top:22px;font-size:12px;font-weight:600;color:var(--white);text-decoration:none;letter-spacing:.5px}
.brand{position:absolute;left:530px;top:0;width:140px;height:140px;border-radius:50%;background:var(--black);border:4px solid var(--white);display:flex;align-items:center;justify-content:center;text-align:center}
.brand span{color:var(--white);font-weight:700;font-size:15px;line-height:19px;width:100px}
.slider{position:absolute;top:480px;left:175px;height:120px;display:flex;gap:6px}
.slide{width:110px;height:120px;font-size:10px;line-height:14px;padding:28px 10px;text-align:center}
.slide.red{background:var(--red);color:var(--white)}
.slide.light{background:var(--white);color:var(--ink)}
.slide.thumb{padding:0}
.slide.bar{width:14px;background:var(--red);padding:0}

/* about */
.about-copy{position:absolute;left:335px;top:722px;width:790px;padding-left:14px;border-left:2px solid var(--line)}
.team-card{position:absolute;top:880px;width:200px}
.team-card .photo{position:static;width:200px;height:180px}
.team-card h4{font-size:13px;font-weight:700;margin-top:12px}
.team-card p{font-size:12px;color:var(--grey);margin-top:4px}
.pager{position:absolute;top:1142px;left:570px;display:flex;gap:12px}
.pager span{width:10px;height:10px;border-radius:50%;background:#bbb}
.pager span.active{background:var(--ink)}

/* works */
.works{position:absolute;left:0;top:1170px;width:1200px;height:620px;background:var(--black);
  clip-path:polygon(0 0,100% 50px,100% 560px,0 620px)}
.arrow-btn{position:absolute;top:1268px;width:26px;height:26px;border-radius:50%;background:var(--white)}
.video-tile{position:absolute;width:210px}
.video-tile .photo{position:relative;width:210px;height:120px}
.video-tile .play{position:absolute;left:10px;bottom:10px;width:26px;height:26px}
.video-tile h5{color:var(--white);font-size:10px;font-weight:700;margin-top:10px;letter-spacing:.4px}

/* ongoing */
.ongoing-copy{position:absolute;left:410px;top:1870px;width:710px;padding-left:14px;border-left:2px solid var(--red)}
.project-photo{position:absolute;width:240px}

/* blog */
.blog{position:absolute;left:0;top:2450px;width:1200px;height:720px;background:var(--black);
  clip-path:polygon(0 40px,100% 0,100% 680px,0 720px)}
.blog-card{position:absolute;top:2600px;width:230px;height:330px;background:var(--card);padding-bottom:14px}
.blog-card.alt{background:var(--card-lite)}
.blog-card .photo{position:static;width:230px;height:120px}
.blog-card h4{color:var(--white);font-size:12px;font-weight:700;line-height:17px;margin:14px 14px 8px}
.blog-card .body-copy{margin:0 14px;font-size:10px;line-height:15px;color:#9a9a9a}
.blog-card .meta{margin:12px 14px 0;font-size:9px;color:#bbb}
.blog-card .meta b{color:var(--red);font-weight:600}

/* portfolio */
.filters{position:absolute;left:390px;top:3222px;display:flex;gap:28px;font-size:10px;font-weight:600;color:var(--grey);letter-spacing:.5px}
.filters .current{color:var(--red)}
.grid-tile{position:absolute;width:240px;height:150px}
.feature-tile{position:absolute;left:240px;top:3310px;width:240px;height:150px;background:var(--red);color:var(--white);padding:16px 18px}
.feature-tile h5{font-size:13px;font-weight:700}
.feature-tile p{font-size:10px;line-height:14px;margin-top:6px;opacity:.9}
.feature-tile small{position:absolute;left:18px;bottom:12px;font-size:9px}

/* contact */
.contact{position:absolute;left:0;top:3920px;width:1200px;height:360px;background:var(--night)}
.contact h6{position:absolute;font-size:11px;font-weight:700;color:var(--white);letter-spacing:.5px}
.address{position:absolute;left:200px;top:4040px;font-size:11px;line-height:20px;color:#bfbfbf}
.address b{color:var(--white);font-weight:700}
.field{position:absolute;left:600px;width:400px;height:32px;background:#262626;border:1px solid #333;font-size:10px;color:#999;padding:9px 12px}
.submit{position:absolute;left:600px;top:4200px;width:80px;height:30px;background:var(--red);color:var(--white);font-size:10px;font-weight:700;text-align:center;line-height:30px}

/* footer */
.footer-title{position:absolute;top:4318px;left:0;width:1200px;text-align:center;font-size:12px;font-weight:700;letter-spacing:.5px}
.socials{position:absolute;top:4355px;left:0;width:1200px;display:flex;justify-content:center;gap:16px}
.socials span{width:40px;height:40px;border-radius:50%;background:var(--black)}
.copyright{position:absolute;top:4440px;left:0;width:1200px;text-align:center;font-size:10px;color:var(--grey)}
</style>
</head>
<body>

<!-- header + hero -->
<section class="hero" role="img" aria-label="Black and white photograph of a railway track curving through dry hills"></section>
<nav class="main-nav">
  <a style="left:180px">HOME</a>
  <a style="left:262px">ABOUT US</a>
  <a style="left:364px">OUR WORKS</a>
  <a style="left:760px">ONGOING</a>
  <a style="left:862px">BLOG</a>
  <a style="left:940px">PORTFOLIO</a>
</nav>
<div class="brand"><span>Copper Lantern Films</span></div>
<div class="slider">
  <div class="slide red">Sed ullam<br>vitae</div>
  <div class="slide thumb" role="img" aria-label="Film still thumbnail" style="background:linear-gradient(135deg,#3c4f7a,#111)"></div>
  <div class="slide thumb" role="img" aria-label="Film still thumbnail" style="background:linear-gradient(135deg,#8a5a2e,#2d1a10)"></div>
  <div class="slide thumb" role="img" aria-label="Film still thumbnail" style="background:linear-gradient(135deg,#b23a2a,#3a2a5a)"></div>
  <div class="slide thumb" role="img" aria-label="Film still thumbnail" style="background:linear-gradient(135deg,#2a5a8a,#0e1e33)"></div>
  <div class="slide bar"></div>
  <div class="slide light">Nisi aute<br>ipsa</div>
  <div class="slide light">Sed ullam<br>vitae</div>
</div>

<!-- about -->
<h2 class="section-title" style="top:732px">About<span class="tag">Us</span></h2>
<p class="about-copy body-copy">Lorem ipsum dolor sit amet, consectetur adipiscing elit, sed diam nonummy nibh euismod tincidunt ut laoreet dolore magna aliquam erat volutpat. Ut wisi enim ad minim veniam, quis nostrud exerci tation ullamcorper suscipit lobortis nisl ut aliquip ex ea commodo consequat. Duis autem vel eum iriure dolor in hendrerit in vulputate velit esse molestie consequat, vel illum dolore eu feugiat nulla facilisis at vero eros et accumsan et iusto odio dignissim qui blandit praesent luptatum zzril delenit augue duis dolore te feugait nulla facilisi.</p>
<div class="dot-nav" style="top:800px"><span class="active"></span><span></span><span></span><span></span><span></span><span></span></div>

<h2 class="section-title" style="top:838px">Our<span class="tag">Team</span></h2>
<div class="team-card" style="left:220px"><div class="photo" role="img" aria-label="Portrait of team member" style="background:linear-gradient(160deg,#cfc3b2,#7a6a58)"></div><h4>HARLAN FITCH</h4><p>Director</p></div>
<div class="team-card" style="left:490px"><div class="photo" role="img" aria-label="Portrait of team member" style="background:linear-gradient(160deg,#e2d7c8,#9b8468)"></div><h4>HARLAN FITCH</h4><p>Director</p></div>
<div class="team-card" style="left:760px"><div class="photo" role="img" aria-label="Portrait of team member" style="background:linear-gradient(160deg,#d8cfc2,#6e5a44)"></div><h4>HARLAN FITCH</h4><p>Director</p></div>
<div class="pager"><span class="active"></span><span></span><span></span></div>

<!-- works -->
<section class="works on-black">
  <div class="dot-nav" style="top:180px"><span></span><span class="active"></span><span></span><span></span><span></span><span></span></div>
</section>
<h2 class="section-title on-dark" style="top:1270px">Our<span class="tag" style="background:var(--white);color:var(--ink)">Works</span></h2>
<svg class="arrow-btn" style="left:322px" viewBox="0 0 26 26"><path d="M15 8l-6 5 6 5z" fill="#111"/></svg>
<svg class="arrow-btn" style="left:354px" viewBox="0 0 26 26"><path d="M11 8l6 5-6 5z" fill="#111"/></svg>

<div class="video-tile" style="left:215px;top:1355px"><div class="photo" role="img" aria-label="Video thumbnail, silhouette at sunset" style="background:linear-gradient(135deg,#f2b53c,#6a3a12)"><svg class="play" viewBox="0 0 26 26"><circle cx="13" cy="13" r="13" fill="#fff"/><path d="M10 8l8 5-8 5z" fill="#111"/></svg></div><h5>LOREM IPSUM DOLOR SIT AMET.</h5></div>
<div class="video-tile" style="left:490px;top:1355px"><div class="photo" role="img" aria-label="Video thumbnail, dancer mid-jump" style="background:linear-gradient(135deg,#e9a86a,#7a4a2a)"><svg class="play" viewBox="0 0 26 26"><circle cx="13" cy="13" r="13" fill="#fff"/><path d="M10 8l8 5-8 5z" fill="#111"/></svg></div><h5>LOREM IPSUM DOLOR SIT AMET.</h5></div>
<div class="video-tile" style="left:765px;top:1355px"><div class="photo" role="img" aria-label="Video thumbnail, fire at night" style="background:linear-gradient(135deg,#1f4f8a,#d2641e)"><svg class="play" viewBox="0 0 26 26"><circle cx="13" cy="13" r="13" fill="#fff"/><path d="M10 8l8 5-8 5z" fill="#111"/></svg></div><h5>LOREM IPSUM DOLOR SIT AMET.</h5></div>
<div class="video-tile" style="left:215px;top:1545px"><div class="photo" role="img" aria-label="Video thumbnail, figure in blue light" style="background:linear-gradient(135deg,#1b3a6a,#c89a3a)"><svg class="play" viewBox="0 0 26 26"><circle cx="13" cy="13" r="13" fill="#fff"/><path d="M10 8l8 5-8 5z" fill="#111"/></svg></div><h5>LOREM IPSUM DOLOR SIT AMET.</h5></div>
<div class="video-tile" style="left:490px;top:1545px"><div class="photo" role="img" aria-label="Video thumbnail, golden field" style="background:linear-gradient(135deg,#f0c040,#8a5a10)"><svg class="play" viewBox="0 0 26 26"><circle cx="13" cy="13" r="13" fill="#fff"/><path d="M10 8l8 5-8 5z" fill="#111"/></svg></div><h5>LOREM IPSUM DOLOR SIT AMET.</h5></div>
<div class="video-tile" style="left:765px;top:1545px"><div class="photo" role="img" aria-label="Video thumbnail, warm orange scene" style="background:linear-gradient(135deg,#e07a20,#5a2a10)"><svg class="play" viewBox="0 0 26 26"><circle cx="13" cy="13" r="13" fill="#fff"/><path d="M10 8l8 5-8 5z" fill="#111"/></svg></div><h5>LOREM IPSUM DOLOR SIT AMET.</h5></div>

<!-- ongoing -->
<h2 class="section-title" style="top:1876px">Ongoing<span class="tag">Projects</span></h2>
<p class="ongoing-copy body-copy">Lorem ipsum dolor sit amet, consectetur adipiscing elit, sed diam nonummy nibh euismod tincidunt ut laoreet dolore magna aliquam erat volutpat. Ut wisi enim ad minim veniam, quis nostrud exerci tation ullamcorper.</p>
<div class="dot-nav" style="top:2150px"><span></span><span></span><span class="active"></span><span></span><span></span><span></span></div>

<div class="photo project-photo" style="left:200px;top:1990px;height:155px;background:linear-gradient(135deg,#3aa04a,#1d5a2a)" role="img" aria-label="Film crew shooting against green screen"></div>
<div class="photo project-photo" style="left:475px;top:1990px;height:155px;background:linear-gradient(180deg,#7fb0e0,#5a7a3a)" role="img" aria-label="Crew on a green hillside"></div>
<div class="photo project-photo" style="left:750px;top:1990px;height:155px;background:linear-gradient(180deg,#6a9ad0,#a08060)" role="img" aria-label="Vehicles and crew in the desert"></div>
<div class="photo project-photo" style="left:200px;top:2190px;height:170px;background:linear-gradient(180deg,#e0b070,#6a4a2a)" role="img" aria-label="Person and dog in a golden field"></div>
<div class="photo project-photo" style="left:475px;top:2190px;height:170px;background:linear-gradient(135deg,#3a3a3a,#b8a890)" role="img" aria-label="Behind the scenes studio lighting"></div>
<div class="photo project-photo" style="left:750px;top:2190px;height:170px;background:linear-gradient(180deg,#8ab0d8,#4a7a3a)" role="img" aria-label="Historic building with gardens"></div>
<div class="btn-outline" style="left:550px;top:2400px;width:100px;color:var(--ink)">Read More</div>

<!-- blog -->
<section class="blog on-black">
  <div class="dot-nav" style="top:230px"><span></span><span></span><span></span><span class="active"></span><span></span><span></span></div>
</section>
<h2 class="section-title on-dark" style="top:2530px">Our<span class="tag" style="background:var(--white);color:var(--ink)">Blog</span></h2>

<article class="blog-card" style="left:205px">
  <div class="photo" role="img" aria-label="Black and white video still with player controls" style="background:linear-gradient(135deg,#9a9a9a,#2a2a2a)"></div>
  <h4>Lorem ipsum dolor sit amet, consectetur adipiscing elit.</h4>
  <p class="body-copy">Nam vitae dolor et fringilla pulvinar, sed dapibus nisi nec lorem facilisis pretium.</p>
  <p class="meta">Category: <b>Films</b> | Comments: <b>12</b></p>
</article>
<article class="blog-card alt" style="left:485px">
  <div class="photo" role="img" aria-label="Black and white photo of a person in a field" style="background:linear-gradient(135deg,#d0d0d0,#4a4a4a)"></div>
  <h4>Lorem ipsum dolor sit amet, consectetur adipiscing elit.</h4>
  <p class="body-copy">Nam vitae dolor et fringilla pulvinar, sed dapibus nisi nec lorem facilisis pretium.</p>
  <p class="meta">Category: <b>Films</b> | Comments: <b>12</b></p>
</article>
<article class="blog-card" style="left:765px">
  <div class="photo" role="img" aria-label="Audio player with waveform" style="background:linear-gradient(180deg,#f2f2f2,#bdbdbd)"></div>
  <h4>Lorem ipsum dolor sit amet, consectetur adipiscing elit.</h4>
  <p class="body-copy">Nam vitae dolor et fringilla pulvinar, sed dapibus nisi nec lorem facilisis pretium.</p>
  <p class="meta">Category: <b>Audio</b> | Comments: <b>12</b></p>
</article>
<div class="btn-outline" style="left:535px;top:3010px;width:130px;color:var(--white)">All Blog Posts</div>

<!-- portfolio -->
<h2 class="section-title" style="top:3215px">Our<span class="tag" style="background:var(--ink)">Portfolio</span></h2>
<div class="filters"><span class="current">ALL</span><span>LANDSCAPE</span><span>PEOPLE</span><span>WEDDINGS</span><span>CITY</span></div>
<div class="dot-nav" style="top:3330px"><span></span><span></span><span></span><span></span><span class="active"></span><span></span></div>

<div class="grid-tile" style="left:0;top:3310px;background:linear-gradient(135deg,#bdbdbd,#1a1a1a)" role="img" aria-label="Black and white landscape photo"></div>
<div class="feature-tile"><h5>Nature Time</h5><p>Lorem ipsum dolor sit amet, consectetur adipiscing elit sed do.</p><small>25 Mar 2014</small></div>
<div class="grid-tile" style="left:480px;top:3310px;background:linear-gradient(135deg,#8a8a8a,#e0e0e0)" role="img" aria-label="Black and white photo of grass"></div>
<div class="grid-tile" style="left:720px;top:3310px;background:linear-gradient(135deg,#4a4a4a,#a0a0a0)" role="img" aria-label="Black and white photo of rocks"></div>
<div class="grid-tile" style="left:960px;top:3310px;background:linear-gradient(135deg,#d8d8d8,#6a6a6a)" role="img" aria-label="Black and white portrait photo"></div>
<div class="grid-tile" style="left:0;top:3460px;background:linear-gradient(135deg,#2a2a2a,#9a9a9a)" role="img" aria-label="Black and white photo of a crowd"></div>
<div class="grid-tile" style="left:240px;top:3460px;background:linear-gradient(135deg,#e8e8e8,#5a5a5a)" role="img" aria-label="Black and white photo of a person walking"></div>
<div class="grid-tile" style="left:480px;top:3460px;background:linear-gradient(135deg,#6a6a6a,#1a1a1a)" role="img" aria-label="Black and white street photo"></div>
<div class="grid-tile" style="left:720px;top:3460px;background:linear-gradient(135deg,#b0b0b0,#3a3a3a)" role="img" aria-label="Black and white photo of a child"></div>
<div class="grid-tile" style="left:960px;top:3460px;background:linear-gradient(135deg,#9a9a9a,#dadada)" role="img" aria-label="Black and white photo of a window"></div>
<div class="grid-tile" style="left:0;top:3610px;background:linear-gradient(135deg,#d0d0d0,#3a3a3a)" role="img" aria-label="Black and white portrait photo"></div>
<div class="grid-tile" style="left:240px;top:3610px;background:linear-gradient(135deg,#5a5a5a,#c0c0c0)" role="img" aria-label="Black and white photo of a roadway"></div>
<div class="grid-tile" style="left:480px;top:3610px;background:linear-gradient(135deg,#efefef,#8a8a8a)" role="img" aria-label="Black and white photo of a lake"></div>
<div class="grid-tile" style="left:720px;top:3610px;background:linear-gradient(135deg,#3a3a3a,#8a8a8a)" role="img" aria-label="Black and white photo of a couple"></div>
<div class="grid-tile" style="left:960px;top:3610px;background:linear-gradient(135deg,#1a1a1a,#7a7a7a)" role="img" aria-label="Black and white night photo"></div>
<div class="grid-tile" style="left:0;top:3760px;background:linear-gradient(135deg,#f0f0f0,#6a6a6a)" role="img" aria-label="Black and white portrait photo"></div>
<div class="grid-tile" style="left:240px;top:3760px;background:linear-gradient(135deg,#7a7a7a,#2a2a2a)" role="img" aria-label="Black and white photo of a building"></div>
<div class="grid-tile" style="left:480px;top:3760px;background:linear-gradient(135deg,#c8c8c8,#4a4a4a)" role="img" aria-label="Black and white photo of a person sitting"></div>
<div class="grid-tile" style="left:720px;top:3760px;background:linear-gradient(135deg,#9a9a9a,#e8e8e8)" role="img" aria-label="Black and white beach photo"></div>
<div class="grid-tile" style="left:960px;top:3760px;background:linear-gradient(135deg,#4a4a4a,#bababa)" role="img" aria-label="Black and white portrait photo"></div>

<!-- contact -->
<section class="contact"></section>
<h2 class="section-title on-dark" style="top:3955px">Contact<span class="tag" style="background:var(--white);color:var(--ink)">Us</span></h2>
<h6 style="left:200px;top:4010px">ADDRESS</h6>
<p class="address">Unit 12, 8 Harbour Row,<br>Fremont Quay<br>Lorem ipsum<br>City Name 123 456<br><br><b>Email:</b> hello@copperlanternfilms.com<br><b>Phone:</b> +1 (555) 014 2280<br><b>Fax:</b> +1 (555) 014 2281</p>
<h6 style="left:600px;top:4010px">SEND A MESSAGE</h6>
<div class="field" style="top:4035px">Enter Your Name</div>
<div class="field" style="top:4077px">Enter Your Best Address</div>
<div class="field" style="top:4119px;height:64px">Enter Your Message</div>
<div class="submit">SUBMIT</div>

<!-- footer -->
<h2 class="footer-title">FOLLOW US</h2>
<div class="socials"><span></span><span></span><span></span><span></span><span></span><span></span><span></span><span></span></div>
<p class="copyright">Copyright 2014 Copper Lantern Films. All right reserved.</p>

</body>
</html>
```